Ridgeline Journeys business card

please see website
www.ridgelinejourneys.comau

info needed on card
Curtis Halvey
Ph
email
Adventure Riding GPS trails

please use my logo and colours off my site

Curtis Halvey
curtis@ridgelinejourneys.com

```html
<!DOCTYPE html>
<html lang="en">
<head>
<meta charset="utf-8">
<title>Ridgeline Journeys business card</title>
<link rel="stylesheet" href="https://fonts.googleapis.com/css2?family=Black+Ops+One&family=Open+Sans:wght@400;700&display=swap">
<style>
  :root {
    --page: #e9e7e3;
    --card: #f6f6f6;
    --ink: #161616;
    --accent: #ece25a;
    --accent-soft: #f4ee96;
    --band: #111111;
    --light-text: #f2f2f2;
  }
  * { box-sizing: border-box; margin: 0; padding: 0; }
  html, body { width: 1200px; height: 902px; overflow: hidden; }
  body { background: var(--page); position: relative; font-family: "Open Sans", sans-serif; }

  .card {
    position: absolute;
    width: 540px;
    height: 310px;
    background: var(--card);
    border-radius: 4px;
    box-shadow: 0 10px 28px rgba(0,0,0,.18);
    overflow: hidden;
  }
  .card--front { left: 80px; top: 100px; }
  .card--back  { left: 580px; top: 492px; }

  .brand {
    position: absolute;
    display: flex;
    align-items: center;
    gap: 22px;
  }
  .brand__dot {
    flex: none;
    border-radius: 50%;
    background: var(--accent);
  }
  .brand__name {
    font-family: "Black Ops One", sans-serif;
    color: var(--ink);
    text-transform: uppercase;
    line-height: .95;
    letter-spacing: 1px;
    white-space: nowrap;
  }

  .card--front .brand { left: 70px; top: 96px; }
  .card--front .brand__dot { width: 110px; height: 110px; }
  .card--front .brand__name { font-size: 46px; }

  .back__shapes { position: absolute; inset: 0; width: 100%; height: 100%; }
  .card--back .brand { left: 150px; top: 36px; }
  .card--back .brand__dot { width: 78px; height: 78px; }
  .card--back .brand__name { font-size: 36px; }

  .contact {
    position: absolute;
    left: 150px;
    top: 230px;
    display: flex;
    align-items: center;
    gap: 14px;
    color: var(--light-text);
    white-space: nowrap;
  }
  .contact__name { font-weight: 700; font-size: 17px; letter-spacing: .3px; }
  .contact__rule { width: 1px; height: 40px; background: var(--light-text); }
  .contact__list { list-style: none; font-size: 11.5px; line-height: 1.6; }
  .contact__list li { display: flex; align-items: center; gap: 6px; }
  .contact__list svg { width: 11px; height: 11px; flex: none; }
</style>
</head>
<body>

  <section class="card card--front" aria-label="Card front">
    <div class="brand">
      <span class="brand__dot"></span>
      <h1 class="brand__name">Ridgeline<br>Journeys</h1>
    </div>
  </section>

  <section class="card card--back" aria-label="Card back">
    <svg class="back__shapes" viewBox="0 0 540 310" preserveAspectRatio="none" aria-hidden="true">
      <path d="M0,310 L0,110 C50,235 190,245 310,185 C410,135 480,112 540,104 L540,310 Z" fill="var(--accent)"/>
      <path d="M0,150 C60,240 190,250 310,192 C410,144 480,122 540,114 L540,126 C470,136 400,160 300,208 C190,258 70,250 0,180 Z" fill="var(--accent-soft)" opacity=".6"/>
      <path d="M100,310 L140,232 C280,226 420,172 540,130 L540,310 Z" fill="var(--band)"/>
    </svg>

    <div class="brand">
      <span class="brand__dot"></span>
      <h2 class="brand__name">Ridgeline<br>Journeys</h2>
    </div>

    <div class="contact">
      <p class="contact__name">Curtis Halvey</p>
      <span class="contact__rule"></span>
      <ul class="contact__list">
        <li>
          <svg viewBox="0 0 12 12"><rect x="0.5" y="2" width="11" height="8" fill="none" stroke="currentColor"/><path d="M0.5,2 L6,7 L11.5,2" fill="none" stroke="currentColor"/></svg>
          curtis@ridgelinejourneys.com
        </li>
        <li>
          <svg viewBox="0 0 12 12"><circle cx="6" cy="6" r="5.2" fill="none" stroke="currentColor"/><ellipse cx="6" cy="6" rx="2.2" ry="5.2" fill="none" stroke="currentColor"/><path d="M1,6 H11" stroke="currentColor"/></svg>
          www.ridgelinejourneys.comau
        </li>
      </ul>
    </div>
  </section>

</body>
</html>
```